2018 Desk Calendar Design with Better Spine, Better Health with Chiropractic

In conjunction with the Federation of Spinal Wellness Malaysia (FSW), we are organizing a 2018 desk calendar design. The cover page and monthly design size is 210mm (H) x 195mm (W). The will be a total of 27 designs including a cover page (front) [Sample 1], cover page (back) Malaysia National & States Holiday 2018 (https://restdaylist.example.my/2018-dates/) [Sample 2], 12 months design (front) [Sample 3 and 4], 12 months design (back) [Sample 5], Last page (2017 and 2019 calendar) [Sample 6].

Below are some recommendations for monthly back cover design. The main theme remain as Better SPINE, Better HEALTH with CHIROPRACTIC. Each month can in collaborate with of the following element:-

Suggestion 1 (Celebration of the Month)
January - New Year
February - Chinese New Year
March -
April -
May - Labour Day
June - Aidilfitri Festival
July-
August - Independent Day
September - Malaysia Day
October - World Spine Day
November - Deepavali Festival
December - Christmas

Suggestion 2 (States in Malaysia)
January - Perlis
February - Kedah
March - Penang
April - Perak
May - Selangor
June - Negeri Sembilan
July- Melaka
August - Johor
September - Pahang
October - Terengganu
November - Kelantan
December - Sabah & Sarawak

Target Market(s)

Chiropractors and Public

Industry/Entity Type

Chiropractor

Colors

Designer to choose colors to be used in the design.

Requirements
Must have
• The theme for the desk calendar design is Better Spine, Better Health with Chiropractic.
• The cover page should include 5th Anniversary element.
Nice to have
• Lunar or Islamic calendar is optional in the Gregorian calendar.
• AI Format
• Footnote of each page www.spinefsw.example.org

```html
<!DOCTYPE html>
<html lang="en">
<head>
<meta charset="utf-8">
<title>Year Calendars 2017 and 2019</title>
<link href="https://fonts.googleapis.com/css2?family=Roboto:wght@400;700&display=swap" rel="stylesheet">
<style>
  :root{
    --ink:#1a1a1a;
    --navy:#2b3190;
    --weekend:#e6e6e6;
    --binding:#222222;
    --paper:#ffffff;
  }
  *{box-sizing:border-box;margin:0;padding:0}
  html,body{width:1200px;height:1115px;overflow:hidden;background:var(--paper)}
  body{position:relative;font-family:"Roboto",Arial,sans-serif;color:var(--ink)}

  .binding{
    position:absolute;left:40px;top:24px;width:1128px;height:28px;
    background:repeating-linear-gradient(90deg,var(--binding) 0 28px,transparent 28px 50px);
  }

  .year{position:absolute;top:168px;width:540px}
  .year--2017{left:40px}
  .year--2019{left:616px}
  .year-title{
    text-align:center;font-weight:700;font-size:30px;color:var(--navy);
    margin-left:-40px;height:80px;line-height:44px;
  }
  .year--2019 .year-title{margin-left:0;padding-left:40px}

  .months{
    display:grid;grid-template-columns:repeat(3,164px);column-gap:23px;
    grid-template-rows:164px 176px 176px auto;list-style:none;
  }
  .month{width:164px}
  .month-name{
    text-align:center;font-size:12px;font-weight:700;color:var(--navy);
    line-height:14px;
  }
  .weekdays,.days{
    display:grid;grid-template-columns:repeat(7,1fr);list-style:none;
    font-size:11px;line-height:17px;padding-left:3px;
  }
  .weekdays{font-weight:700;color:var(--navy);line-height:15px}
  .days{
    background:linear-gradient(90deg,var(--weekend) 0 14.28%,transparent 14.28% 85.72%,var(--weekend) 85.72%);
  }
  .s1 li:first-child{grid-column-start:2}
  .s2 li:first-child{grid-column-start:3}
  .s3 li:first-child{grid-column-start:4}
  .s4 li:first-child{grid-column-start:5}
  .s5 li:first-child{grid-column-start:6}
  .s6 li:first-child{grid-column-start:7}
</style>
</head>
<body>
<div class="binding" aria-hidden="true"></div>

<section class="year year--2017">
  <h2 class="year-title">2017</h2>
  <ol class="months">
    <li class="month"><h3 class="month-name">January</h3><ul class="weekdays"><li>S<li>M<li>T<li>W<li>T<li>F<li>S</ul>
      <ol class="days s0"><li>1<li>2<li>3<li>4<li>5<li>6<li>7<li>8<li>9<li>10<li>11<li>12<li>13<li>14<li>15<li>16<li>17<li>18<li>19<li>20<li>21<li>22<li>23<li>24<li>25<li>26<li>27<li>28<li>29<li>30<li>31</ol></li>
    <li class="month"><h3 class="month-name">February</h3><ul class="weekdays"><li>S<li>M<li>T<li>W<li>T<li>F<li>S</ul>
      <ol class="days s3"><li>1<li>2<li>3<li>4<li>5<li>6<li>7<li>8<li>9<li>10<li>11<li>12<li>13<li>14<li>15<li>16<li>17<li>18<li>19<li>20<li>21<li>22<li>23<li>24<li>25<li>26<li>27<li>28</ol></li>
    <li class="month"><h3 class="month-name">March</h3><ul class="weekdays"><li>S<li>M<li>T<li>W<li>T<li>F<li>S</ul>
      <ol class="days s3"><li>1<li>2<li>3<li>4<li>5<li>6<li>7<li>8<li>9<li>10<li>11<li>12<li>13<li>14<li>15<li>16<li>17<li>18<li>19<li>20<li>21<li>22<li>23<li>24<li>25<li>26<li>27<li>28<li>29<li>30<li>31</ol></li>
    <li class="month"><h3 class="month-name">April</h3><ul class="weekdays"><li>S<li>M<li>T<li>W<li>T<li>F<li>S</ul>
      <ol class="days s6"><li>1<li>2<li>3<li>4<li>5<li>6<li>7<li>8<li>9<li>10<li>11<li>12<li>13<li>14<li>15<li>16<li>17<li>18<li>19<li>20<li>21<li>22<li>23<li>24<li>25<li>26<li>27<li>28<li>29<li>30</ol></li>
    <li class="month"><h3 class="month-name">May</h3><ul class="weekdays"><li>S<li>M<li>T<li>W<li>T<li>F<li>S</ul>
      <ol class="days s1"><li>1<li>2<li>3<li>4<li>5<li>6<li>7<li>8<li>9<li>10<li>11<li>12<li>13<li>14<li>15<li>16<li>17<li>18<li>19<li>20<li>21<li>22<li>23<li>24<li>25<li>26<li>27<li>28<li>29<li>30<li>31</ol></li>
    <li class="month"><h3 class="month-name">June</h3><ul class="weekdays"><li>S<li>M<li>T<li>W<li>T<li>F<li>S</ul>
      <ol class="days s4"><li>1<li>2<li>3<li>4<li>5<li>6<li>7<li>8<li>9<li>10<li>11<li>12<li>13<li>14<li>15<li>16<li>17<li>18<li>19<li>20<li>21<li>22<li>23<li>24<li>25<li>26<li>27<li>28<li>29<li>30</ol></li>
    <li class="month"><h3 class="month-name">July</h3><ul class="weekdays"><li>S<li>M<li>T<li>W<li>T<li>F<li>S</ul>
      <ol class="days s6"><li>1<li>2<li>3<li>4<li>5<li>6<li>7<li>8<li>9<li>10<li>11<li>12<li>13<li>14<li>15<li>16<li>17<li>18<li>19<li>20<li>21<li>22<li>23<li>24<li>25<li>26<li>27<li>28<li>29<li>30<li>31</ol></li>
    <li class="month"><h3 class="month-name">August</h3><ul class="weekdays"><li>S<li>M<li>T<li>W<li>T<li>F<li>S</ul>
      <ol class="days s2"><li>1<li>2<li>3<li>4<li>5<li>6<li>7<li>8<li>9<li>10<li>11<li>12<li>13<li>14<li>15<li>16<li>17<li>18<li>19<li>20<li>21<li>22<li>23<li>24<li>25<li>26<li>27<li>28<li>29<li>30<li>31</ol></li>
    <li class="month"><h3 class="month-name">September</h3><ul class="weekdays"><li>S<li>M<li>T<li>W<li>T<li>F<li>S</ul>
      <ol class="days s5"><li>1<li>2<li>3<li>4<li>5<li>6<li>7<li>8<li>9<li>10<li>11<li>12<li>13<li>14<li>15<li>16<li>17<li>18<li>19<li>20<li>21<li>22<li>23<li>24<li>25<li>26<li>27<li>28<li>29<li>30</ol></li>
    <li class="month"><h3 class="month-name">October</h3><ul class="weekdays"><li>S<li>M<li>T<li>W<li>T<li>F<li>S</ul>
      <ol class="days s0"><li>1<li>2<li>3<li>4<li>5<li>6<li>7<li>8<li>9<li>10<li>11<li>12<li>13<li>14<li>15<li>16<li>17<li>18<li>19<li>20<li>21<li>22<li>23<li>24<li>25<li>26<li>27<li>28<li>29<li>30<li>31</ol></li>
    <li class="month"><h3 class="month-name">November</h3><ul class="weekdays"><li>S<li>M<li>T<li>W<li>T<li>F<li>S</ul>
      <ol class="days s3"><li>1<li>2<li>3<li>4<li>5<li>6<li>7<li>8<li>9<li>10<li>11<li>12<li>13<li>14<li>15<li>16<li>17<li>18<li>19<li>20<li>21<li>22<li>23<li>24<li>25<li>26<li>27<li>28<li>29<li>30</ol></li>
    <li class="month"><h3 class="month-name">December</h3><ul class="weekdays"><li>S<li>M<li>T<li>W<li>T<li>F<li>S</ul>
      <ol class="days s5"><li>1<li>2<li>3<li>4<li>5<li>6<li>7<li>8<li>9<li>10<li>11<li>12<li>13<li>14<li>15<li>16<li>17<li>18<li>19<li>20<li>21<li>22<li>23<li>24<li>25<li>26<li>27<li>28<li>29<li>30<li>31</ol></li>
  </ol>
</section>

<section class="year year--2019">
  <h2 class="year-title">2019</h2>
  <ol class="months">
    <li class="month"><h3 class="month-name">January</h3><ul class="weekdays"><li>S<li>M<li>T<li>W<li>T<li>F<li>S</ul>
      <ol class="days s2"><li>1<li>2<li>3<li>4<li>5<li>6<li>7<li>8<li>9<li>10<li>11<li>12<li>13<li>14<li>15<li>16<li>17<li>18<li>19<li>20<li>21<li>22<li>23<li>24<li>25<li>26<li>27<li>28<li>29<li>30<li>31</ol></li>
    <li class="month"><h3 class="month-name">February</h3><ul class="weekdays"><li>S<li>M<li>T<li>W<li>T<li>F<li>S</ul>
      <ol class="days s5"><li>1<li>2<li>3<li>4<li>5<li>6<li>7<li>8<li>9<li>10<li>11<li>12<li>13<li>14<li>15<li>16<li>17<li>18<li>19<li>20<li>21<li>22<li>23<li>24<li>25<li>26<li>27<li>28</ol></li>
    <li class="month"><h3 class="month-name">March</h3><ul class="weekdays"><li>S<li>M<li>T<li>W<li>T<li>F<li>S</ul>
      <ol class="days s5"><li>1<li>2<li>3<li>4<li>5<li>6<li>7<li>8<li>9<li>10<li>11<li>12<li>13<li>14<li>15<li>16<li>17<li>18<li>19<li>20<li>21<li>22<li>23<li>24<li>25<li>26<li>27<li>28<li>29<li>30<li>31</ol></li>
    <li class="month"><h3 class="month-name">April</h3><ul class="weekdays"><li>S<li>M<li>T<li>W<li>T<li>F<li>S</ul>
      <ol class="days s1"><li>1<li>2<li>3<li>4<li>5<li>6<li>7<li>8<li>9<li>10<li>11<li>12<li>13<li>14<li>15<li>16<li>17<li>18<li>19<li>20<li>21<li>22<li>23<li>24<li>25<li>26<li>27<li>28<li>29<li>30</ol></li>
    <li class="month"><h3 class="month-name">May</h3><ul class="weekdays"><li>S<li>M<li>T<li>W<li>T<li>F<li>S</ul>
      <ol class="days s3"><li>1<li>2<li>3<li>4<li>5<li>6<li>7<li>8<li>9<li>10<li>11<li>12<li>13<li>14<li>15<li>16<li>17<li>18<li>19<li>20<li>21<li>22<li>23<li>24<li>25<li>26<li>27<li>28<li>29<li>30<li>31</ol></li>
    <li class="month"><h3 class="month-name">June</h3><ul class="weekdays"><li>S<li>M<li>T<li>W<li>T<li>F<li>S</ul>
      <ol class="days s6"><li>1<li>2<li>3<li>4<li>5<li>6<li>7<li>8<li>9<li>10<li>11<li>12<li>13<li>14<li>15<li>16<li>17<li>18<li>19<li>20<li>21<li>22<li>23<li>24<li>25<li>26<li>27<li>28<li>29<li>30</ol></li>
    <li class="month"><h3 class="month-name">July</h3><ul class="weekdays"><li>S<li>M<li>T<li>W<li>T<li>F<li>S</ul>
      <ol class="days s1"><li>1<li>2<li>3<li>4<li>5<li>6<li>7<li>8<li>9<li>10<li>11<li>12<li>13<li>14<li>15<li>16<li>17<li>18<li>19<li>20<li>21<li>22<li>23<li>24<li>25<li>26<li>27<li>28<li>29<li>30<li>31</ol></li>
    <li class="month"><h3 class="month-name">August</h3><ul class="weekdays"><li>S<li>M<li>T<li>W<li>T<li>F<li>S</ul>
      <ol class="days s4"><li>1<li>2<li>3<li>4<li>5<li>6<li>7<li>8<li>9<li>10<li>11<li>12<li>13<li>14<li>15<li>16<li>17<li>18<li>19<li>20<li>21<li>22<li>23<li>24<li>25<li>26<li>27<li>28<li>29<li>30<li>31</ol></li>
    <li class="month"><h3 class="month-name">September</h3><ul class="weekdays"><li>S<li>M<li>T<li>W<li>T<li>F<li>S</ul>
      <ol class="days s0"><li>1<li>2<li>3<li>4<li>5<li>6<li>7<li>8<li>9<li>10<li>11<li>12<li>13<li>14<li>15<li>16<li>17<li>18<li>19<li>20<li>21<li>22<li>23<li>24<li>25<li>26<li>27<li>28<li>29<li>30</ol></li>
    <li class="month"><h3 class="month-name">October</h3><ul class="weekdays"><li>S<li>M<li>T<li>W<li>T<li>F<li>S</ul>
      <ol class="days s2"><li>1<li>2<li>3<li>4<li>5<li>6<li>7<li>8<li>9<li>10<li>11<li>12<li>13<li>14<li>15<li>16<li>17<li>18<li>19<li>20<li>21<li>22<li>23<li>24<li>25<li>26<li>27<li>28<li>29<li>30<li>31</ol></li>
    <li class="month"><h3 class="month-name">November</h3><ul class="weekdays"><li>S<li>M<li>T<li>W<li>T<li>F<li>S</ul>
      <ol class="days s5"><li>1<li>2<li>3<li>4<li>5<li>6<li>7<li>8<li>9<li>10<li>11<li>12<li>13<li>14<li>15<li>16<li>17<li>18<li>19<li>20<li>21<li>22<li>23<li>24<li>25<li>26<li>27<li>28<li>29<li>30</ol></li>
    <li class="month"><h3 class="month-name">December</h3><ul class="weekdays"><li>S<li>M<li>T<li>W<li>T<li>F<li>S</ul>
      <ol class="days s0"><li>1<li>2<li>3<li>4<li>5<li>6<li>7<li>8<li>9<li>10<li>11<li>12<li>13<li>14<li>15<li>16<li>17<li>18<li>19<li>20<li>21<li>22<li>23<li>24<li>25<li>26<li>27<li>28<li>29<li>30<li>31</ol></li>
  </ol>
</section>
</body>
</html>
```